Wholesale in Gold Jewellery & Gold Bullion

We are an established gold jewellery and gold bullion wholesaler selling these products to international clients. We already have a name and logo of our company, hence please view attached current card design. We need a completely new design to compliment our business and industry and the final design should be new and elegant.

Contact Information for Business Card

New card details must be same as per current card. Like logo, name, tel no. & etc.

Colors

Designer to choose colors to be used in the design.

```html
<!DOCTYPE html>
<html lang="en">
<head>
<meta charset="utf-8">
<title>Harlow &amp; Co – Business Card</title>
<link href="https://fonts.googleapis.com/css2?family=Montserrat:wght@500;600&family=Tinos:wght@700&display=swap" rel="stylesheet">
<style>
  :root {
    --bg: #e4e5e7;
    --card: #ffffff;
    --ink: #141414;
    --gold: #eba224;
    --gold-line: #e39a1c;
  }
  html, body {
    margin: 0;
    width: 1200px;
    height: 800px;
    overflow: hidden;
    background: var(--bg);
  }
  .card {
    position: absolute;
    left: 75px;
    top: 100px;
    width: 1050px;
    height: 600px;
    background: var(--card);
    box-shadow: 0 6px 24px rgba(0,0,0,0.12);
  }
  .company-name {
    position: absolute;
    left: 60px;
    top: 42px;
    margin: 0;
    font-family: "Tinos", "Times New Roman", serif;
    font-weight: 700;
    font-size: 44px;
    letter-spacing: 1px;
    color: var(--ink);
  }
  .company-address {
    position: absolute;
    left: 60px;
    top: 102px;
    margin: 0;
    font-family: "Montserrat", Arial, sans-serif;
    font-weight: 500;
    font-size: 23px;
    color: var(--ink);
  }
  .person {
    position: absolute;
    left: 40px;
    top: 160px;
    padding-left: 22px;
    border-left: 8px solid var(--gold);
    font-family: "Montserrat", Arial, sans-serif;
    color: var(--ink);
  }
  .person-name {
    margin: 0;
    font-weight: 500;
    font-size: 38px;
    line-height: 1.1;
  }
  .person-role {
    margin: 2px 0 0 -22px;
    font-weight: 500;
    font-size: 25px;
  }
  .accent-lines {
    position: absolute;
    left: 0;
    top: 0;
  }
  .contact-list {
    position: absolute;
    left: 48px;
    top: 370px;
    margin: 0;
    padding: 0;
    list-style: none;
    font-family: "Montserrat", Arial, sans-serif;
    font-weight: 500;
    font-size: 24px;
    color: var(--ink);
  }
  .contact-list li {
    display: flex;
    align-items: center;
    height: 40px;
  }
  .contact-icon {
    width: 22px;
    height: 22px;
    margin-right: 14px;
    flex: none;
  }
  .brand-mark {
    position: absolute;
    left: 720px;
    top: 248px;
    width: 170px;
    height: 170px;
    border: 16px solid var(--gold);
    border-radius: 50%;
    box-sizing: border-box;
    background: var(--card);
    display: flex;
    align-items: center;
    justify-content: center;
    font-family: "Montserrat", Arial, sans-serif;
    font-weight: 600;
    font-size: 22px;
    letter-spacing: 1px;
    color: var(--gold);
  }
</style>
</head>
<body>
  <div class="card">
    <h1 class="company-name">HARLOW &amp; CO PTE LTD</h1>
    <p class="company-address">18 Lorne Crescent Rd, Singapore 208810</p>

    <div class="person">
      <p class="person-name">Ravin Kesavan</p>
      <p class="person-role">Director</p>
    </div>

    <svg class="accent-lines" width="1050" height="600" viewBox="0 0 1050 600" aria-hidden="true">
      <g stroke="var(--gold-line)" stroke-width="3">
        <line x1="50" y1="296" x2="1000" y2="296"/>
        <line x1="50" y1="314" x2="1000" y2="314"/>
      </g>
    </svg>

    <div class="brand-mark">HARLOW</div>

    <ul class="contact-list">
      <li>
        <svg class="contact-icon" viewBox="0 0 24 24" aria-hidden="true"><path fill="var(--gold)" d="M6.6 10.8a15 15 0 0 0 6.6 6.6l2.2-2.2c.3-.3.7-.4 1-.2 1.1.4 2.3.6 3.6.6.6 0 1 .4 1 1V20c0 .6-.4 1-1 1A17 17 0 0 1 3 4c0-.6.4-1 1-1h3.5c.6 0 1 .4 1 1 0 1.3.2 2.5.6 3.6.1.3 0 .7-.2 1z"/></svg>
        +65 6100 2400
      </li>
      <li>
        <svg class="contact-icon" viewBox="0 0 24 24" aria-hidden="true"><rect x="6" y="2" width="12" height="20" rx="2" fill="none" stroke="var(--gold)" stroke-width="2"/><circle cx="12" cy="18" r="1.2" fill="var(--gold)"/></svg>
        +65 9100 5522
      </li>
      <li>
        <svg class="contact-icon" viewBox="0 0 24 24" aria-hidden="true"><rect x="7" y="2" width="10" height="6" fill="var(--gold)"/><rect x="3" y="9" width="18" height="8" rx="1" fill="var(--gold)"/><rect x="7" y="15" width="10" height="7" fill="var(--gold)" stroke="#fff" stroke-width="1.5"/></svg>
        +65 6100 2411
      </li>
      <li>
        <svg class="contact-icon" viewBox="0 0 24 24" aria-hidden="true"><rect x="2" y="5" width="20" height="14" fill="var(--gold)"/><path d="M2 5l10 8 10-8" fill="none" stroke="#fff" stroke-width="1.5"/></svg>
        ravin@harlowco.com
      </li>
    </ul>
  </div>
</body>
</html>
```